High-Converting Facebook Ads for Portals Drapes & Louvres (6 Products)

We are looking for a graphic designer to create high-quality Facebook & Instagram ads for our business: Portals Drapes and Louvres (Melbourne, Australia).

We require 6 separate ad designs, each for a different product:

Zipscreen Blinds

Outdoor Awnings

Plantation Shutters

Roller Shutters

Security Doors

Roller Blinds & Sheer Curtains

Ad Specifications:

Sizes:

1440 x 1800 px (4:5 ratio)

1080 x 1080 px (1:1 ratio)

1080 x 1920 px (9:16 ratio for Stories/Reels)

Format: PNG (high resolution, not blurry)

Designed specifically for Meta (Facebook/Instagram ads)

Mobile-friendly layout (clear, easy to read)

Style:

Bold, sales-driven, retail-style ads (NOT minimal)

Eye-catching and designed to generate leads

Clean, professional layout

Similar to promotional home improvement ads

Brand Colours:

Red: #E31E24

Blue: #0072BC

White backgrounds

Each ad must include:

“SALE NOW ON” banner at top

Our showroom address:
482 Upper Wattleby Road, Kestrel Heights (must be fully visible, not cut off)

Phone number: 9471 2658

Our logo (provided)

Badge: “Celebrating 13 YEARS in Business” (must be clean and readable)

Call to Action:

For 5 ads: “Book a FREE quote TODAY!”

For Security Doors ad: “ORDER NOW”

Offers / Pricing:

Most products: “UP TO 40% OFF”

Plantation Shutters: “FROM $299/sqm”

Security Doors: “FROM $750”

Content for each ad (examples):

Zipscreen Blinds:

Made to Measure

Fully Installed

Wind, Sun & Insect Protection

Outdoor Awnings:

Reduce Heat & Glare

Energy Saving

Custom Made

Plantation Shutters:

Modern & Elegant

Light & Privacy Control

Durable & Easy Care

Roller Shutters:

Security Protection

Block Heat & Noise

Total Light Control

Security Doors:

3 Point Locking

Premium Mesh

Custom Made

Blinds & Sheers:

Huge Range of Fabrics

Modern Soft Finish

Perfect for Any Room

Important Notes:

All text must be sharp and easy to read (no blur)

Layout must be balanced and not overcrowded

Ensure no text is cut off (especially address and headings)

Badge text must be straight and professional (no distortion)

Use high-quality, relevant images (we will provide references)

Goal:
Create ads that look professional, trustworthy, and generate enquiries/bookings for in-home quotes.

We are open to creative ideas but want a strong, bold retail-style ad that converts.
I have uploaed chatgpt mocks

Target Market(s)

Homeowners in Melbourne, Australia (typically aged 30–65) looking to improve their homes with blinds, shutters, awnings and security doors. Mid to high income households focused on quality, security, and modern home upgrades.

Industry/Entity Type

Home Improvement / Construction / Retail

Font styles to use
Sans Serif

Requirements
Must have
• Clear, bold and easy-to-read text (must be readable on mobile) High-quality, non-blurry design Strong “SALE” style layout (retail promotional look) Proper spacing (no overcrowded designs) All key info visible (address must NOT be cut off) Correct pricing and offers included Clean “13 YEARS” badge (no distortion or curved text) Consistent branding across all 6 ads
Nice to have
• Modern, slightly premium feel while still being bold Good use of contrast (red/blue/white) Subtle shadows or layering to improve depth Clean use of icons or bullet points Strong hierarchy (headline → benefits → offer → CTA) Variations in layout for testing different ad styles
Should not have
• Minimal or plain designs (we want bold, sales-driven ads) Hard-to-read fonts or script fonts Low-quality or blurry images Overcrowded layouts with too much text Important text cut off (especially address or headings) Overuse of effects or “cheap” looking graphics Yellow-heavy colour schemes (must follow brand colours)

```html
<!DOCTYPE html>
<html lang="en">
<head>
<meta charset="utf-8">
<title>Portals Drapes &amp; Louvres – Sale Ads 4:5</title>
<link href="https://fonts.googleapis.com/css2?family=Anton&family=Oswald:wght@600&family=Poppins:wght@500;600;700;800;900&display=swap" rel="stylesheet">
<style>
  :root{
    --red:#e31e24;
    --blue:#0072bc;
    --blue-deep:#0b4ea2;
    --white:#ffffff;
    --ink:#1b1b1b;
    --board:#2d2d2d;
    --gold:#e0a91e;
    --gold-dark:#a8750c;
    --grey:#ececec;
  }
  *{box-sizing:border-box;margin:0;padding:0}
  html,body{width:1200px;height:1056px;overflow:hidden;background:var(--board)}
  body{position:relative;font-family:"Poppins",sans-serif;color:var(--ink)}
  .board-title{position:absolute;top:34px;left:0;width:1200px;text-align:center;color:#f2f2f2;font:500 29px "Poppins",sans-serif}

  .ad{position:absolute;width:346px;height:431px;background:var(--white);overflow:hidden}
  .c1{left:56px}.c2{left:430px}.c3{left:804px}
  .r1{top:110px}.r2{top:566px}

  .sale-band{position:absolute;left:0;top:0;width:346px;height:62px;background:var(--red);color:var(--white);font:900 39px/62px "Poppins",sans-serif;text-align:center;letter-spacing:-.5px}
  .title-band{position:absolute;left:0;top:64px;width:346px;height:62px;background:linear-gradient(180deg,var(--blue) 0%,var(--blue-deep) 100%);border-top:2px solid var(--white)}
  .product-name{position:absolute;left:14px;top:4px;color:var(--white);font:600 31px/40px "Oswald",sans-serif;white-space:nowrap}
  .product-name.long{font-size:27px;top:6px}
  .site{position:absolute;left:14px;top:44px;color:var(--white);font:500 8.6px "Poppins",sans-serif;letter-spacing:1.3px}

  .badge{position:absolute;left:228px;top:48px;width:108px;height:108px}

  .frame{position:absolute;left:146px;top:134px;width:200px;height:208px;background:var(--blue)}
  .frame-gap{position:absolute;left:164px;top:147px;width:182px;height:195px;background:var(--white)}
  .photo{position:absolute;left:170px;top:156px;width:176px;height:184px}

  .features{position:absolute;left:15px;top:134px;width:122px;list-style:none}
  .features li{display:flex;align-items:center;height:47px;border-bottom:1px solid #d5d5d5}
  .features li:last-child{border-bottom:none}
  .icon{flex:0 0 38px;width:38px;height:38px;margin-left:5px}
  .features span{margin-left:14px;font:500 10px/12.3px "Poppins",sans-serif;color:var(--ink)}

  .offer{position:absolute;left:12px;top:278px;width:132px;height:66px}
  .offer .tag{position:absolute;left:-14px;top:23px;width:52px;transform:rotate(-90deg);color:var(--blue);font:800 13px/15px "Poppins",sans-serif;text-align:center;letter-spacing:.5px}
  .offer .big{position:absolute;left:20px;top:-6px;color:var(--red);font:400 58px/70px "Anton",sans-serif}
  .offer .pct{position:absolute;left:88px;top:-1px;color:var(--red);font:400 30px/34px "Anton",sans-serif}
  .offer .off{position:absolute;left:88px;top:33px;color:var(--red);font:400 21px/26px "Anton",sans-serif}
  .offer .price{position:absolute;left:20px;top:-6px;color:var(--red);font:400 46px/56px "Anton",sans-serif}
  .offer .per{position:absolute;left:21px;top:44px;color:var(--red);font:800 17px/20px "Poppins",sans-serif}
  .offer .price.solo{font-size:54px;line-height:70px;top:-8px}

  .brand{position:absolute;left:0;top:347px;width:146px;height:84px;background:linear-gradient(180deg,#f7f7f7,var(--grey));display:flex;flex-direction:column;align-items:center;justify-content:center;gap:6px}
  .brand-mark{width:22px;height:22px;background:var(--red)}
  .brand-name{color:var(--blue);font:700 13px/14px "Poppins",sans-serif;text-align:center}

  .cta{position:absolute;left:147px;top:347px;width:199px;height:84px;background:var(--red);padding:4px 0 0 4px}
  .cta-line{height:22px;background:var(--blue-deep);color:var(--white);font:700 12.4px/22px "Poppins",sans-serif;text-align:center}
  .cta-line.order{font:800 19px/22px "Poppins",sans-serif;letter-spacing:.3px}
  .phone{display:flex;align-items:center;gap:7px;height:33px;padding-left:12px;color:var(--white);font:800 25px/33px "Poppins",sans-serif}
  .phone svg{width:22px;height:22px}
  .address{display:flex;align-items:center;gap:3px;height:25px;background:var(--blue);color:var(--white);font:600 7.6px/25px "Poppins",sans-serif;padding-left:12px;white-space:nowrap}
  .address svg{width:7px;height:9px}
</style>
</head>
<body>

<svg width="0" height="0" style="position:absolute" aria-hidden="true">
  <defs>
    <linearGradient id="gold" x1="0" y1="0" x2="1" y2="1">
      <stop offset="0" stop-color="#f6cf4a"/><stop offset=".5" stop-color="#d99c15"/><stop offset="1" stop-color="#a8750c"/>
    </linearGradient>
    <symbol id="seal" viewBox="0 0 108 108">
      <circle cx="54" cy="54" r="52" fill="url(#gold)"/>
      <circle cx="54" cy="54" r="46" fill="none" stroke="#fff3c0" stroke-width="1.5"/>
      <circle cx="54" cy="54" r="39" fill="#1b1b1b"/>
      <text x="54" y="39" text-anchor="middle" fill="#f3c23a" font-family="Poppins,sans-serif" font-weight="800" font-size="8">CELEBRATING</text>
      <text x="54" y="61" text-anchor="middle" fill="#ffffff" font-family="Oswald,sans-serif" font-weight="600" font-size="19">13 YEARS</text>
      <text x="54" y="77" text-anchor="middle" fill="#f3c23a" font-family="Poppins,sans-serif" font-weight="800" font-size="8">IN BUSINESS</text>
    </symbol>
    <symbol id="tick-icon" viewBox="0 0 38 38">
      <circle cx="19" cy="19" r="18" fill="var(--blue)" stroke="var(--red)" stroke-width="1.5"/>
      <path d="M11 19.5l5.5 5.5L27 14" fill="none" stroke="#fff" stroke-width="3" stroke-linecap="round" stroke-linejoin="round"/>
    </symbol>
    <symbol id="phone-icon" viewBox="0 0 22 22">
      <circle cx="11" cy="11" r="10.5" fill="#fff"/>
      <path d="M7.2 5.5l2 .1 1 2.8-1.3 1.1a7 7 0 0 0 3.6 3.6l1.1-1.3 2.8 1v2a1.4 1.4 0 0 1-1.5 1.3A10 10 0 0 1 5.8 7a1.4 1.4 0 0 1 1.4-1.5z" fill="var(--red)"/>
    </symbol>
    <symbol id="pin-icon" viewBox="0 0 7 9">
      <path d="M3.5 0A3 3 0 0 0 .5 3c0 2.2 3 6 3 6s3-3.8 3-6a3 3 0 0 0-3-3zm0 4.2a1.2 1.2 0 1 1 0-2.4 1.2 1.2 0 0 1 0 2.4z" fill="#fff"/>
    </symbol>
  </defs>
</svg>

<h1 class="board-title">1440 x 1800 px (4:5 ratio)</h1>

<!-- Zipscreen Blinds -->
<section class="ad c1 r1">
  <div class="sale-band">SALE NOW ON</div>
  <div class="title-band"><h2 class="product-name">Zipscreen Blinds</h2><p class="site">www.portalsdrapesandlouvres.com.au</p></div>
  <div class="frame"></div><div class="frame-gap"></div>
  <div class="photo" role="img" aria-label="Patio enclosed by zipscreen blinds overlooking a lawn" style="background:linear-gradient(180deg,#b9a48a 0%,#7d8c6a 45%,#5d8f3a 70%,#4b3a2c 100%)"></div>
  <ul class="features">
    <li><svg class="icon"><use href="#tick-icon"/></svg><span>Made to<br>Measure</span></li>
    <li><svg class="icon"><use href="#tick-icon"/></svg><span>Fully<br>Installed</span></li>
    <li><svg class="icon"><use href="#tick-icon"/></svg><span>Wind, Sun<br>&amp; Insect<br>Protection</span></li>
  </ul>
  <div class="offer"><div class="tag">UP TO</div><div class="big">40</div><div class="pct">%</div><div class="off">OFF</div></div>
  <svg class="badge"><use href="#seal"/></svg>
  <div class="brand"><div class="brand-mark"></div><div class="brand-name">Portals Drapes<br>&amp; Louvres</div></div>
  <div class="cta"><div class="cta-line">Book a FREE quote TODAY!</div><div class="phone"><svg><use href="#phone-icon"/></svg>9471 2658</div><div class="address"><svg><use href="#pin-icon"/></svg>482 Upper Wattleby Road, Kestrel Heights</div></div>
</section>

<!-- Outdoor Awnings -->
<section class="ad c2 r1">
  <div class="sale-band">SALE NOW ON</div>
  <div class="title-band"><h2 class="product-name">Outdoor Awnings</h2><p class="site">www.portalsdrapesandlouvres.com.au</p></div>
  <div class="frame"></div><div class="frame-gap"></div>
  <div class="photo" role="img" aria-label="Striped green and white awnings over windows of a red brick house" style="background:linear-gradient(160deg,#dfe3e6 0%,#3f6b4f 30%,#a24a32 55%,#d8cfb4 80%,#6f6f6a 100%)"></div>
  <ul class="features">
    <li><svg class="icon"><use href="#tick-icon"/></svg><span>Reduce<br>Heat &amp; Glare</span></li>
    <li><svg class="icon"><use href="#tick-icon"/></svg><span>Energy<br>Saving</span></li>
    <li><svg class="icon"><use href="#tick-icon"/></svg><span>Custom<br>Made</span></li>
  </ul>
  <div class="offer"><div class="tag">UP TO</div><div class="big">40</div><div class="pct">%</div><div class="off">OFF</div></div>
  <svg class="badge"><use href="#seal"/></svg>
  <div class="brand"><div class="brand-mark"></div><div class="brand-name">Portals Drapes<br>&amp; Louvres</div></div>
  <div class="cta"><div class="cta-line">Book a FREE quote TODAY!</div><div class="phone"><svg><use href="#phone-icon"/></svg>9471 2658</div><div class="address"><svg><use href="#pin-icon"/></svg>482 Upper Wattleby Road, Kestrel Heights</div></div>
</section>

<!-- Plantation Shutters -->
<section class="ad c3 r1">
  <div class="sale-band">SALE NOW ON</div>
  <div class="title-band"><h2 class="product-name long">Plantation Shutters</h2><p class="site">www.portalsdrapesandlouvres.com.au</p></div>
  <div class="frame"></div><div class="frame-gap"></div>
  <div class="photo" role="img" aria-label="Bedroom with white plantation shutters and timber floor" style="background:linear-gradient(180deg,#cfd6dc 0%,#b4bcc4 45%,#6c6f78 65%,#7a4a2a 100%)"></div>
  <ul class="features">
    <li><svg class="icon"><use href="#tick-icon"/></svg><span>Modern<br>&amp; Elegant</span></li>
    <li><svg class="icon"><use href="#tick-icon"/></svg><span>Light &amp;<br>Privacy<br>Control</span></li>
    <li><svg class="icon"><use href="#tick-icon"/></svg><span>Durable<br>&amp; Easy Care</span></li>
  </ul>
  <div class="offer"><div class="tag">FROM</div><div class="price">$299</div><div class="per">PER SQM</div></div>
  <svg class="badge"><use href="#seal"/></svg>
  <div class="brand"><div class="brand-mark"></div><div class="brand-name">Portals Drapes<br>&amp; Louvres</div></div>
  <div class="cta"><div class="cta-line">Book a FREE quote TODAY!</div><div class="phone"><svg><use href="#phone-icon"/></svg>9471 2658</div><div class="address"><svg><use href="#pin-icon"/></svg>482 Upper Wattleby Road, Kestrel Heights</div></div>
</section>

<!-- Roller Shutters -->
<section class="ad c1 r2">
  <div class="sale-band">SALE NOW ON</div>
  <div class="title-band"><h2 class="product-name">Roller Shutters</h2><p class="site">www.portalsdrapesandlouvres.com.au</p></div>
  <div class="frame"></div><div class="frame-gap"></div>
  <div class="photo" role="img" aria-label="Dark roller shutter fitted over a window on a brick home" style="background:linear-gradient(180deg,#cfcfcf 0%,#55585c 30%,#3c3e42 65%,#c89a6a 100%)"></div>
  <ul class="features">
    <li><svg class="icon"><use href="#tick-icon"/></svg><span>Security<br>Protection</span></li>
    <li><svg class="icon"><use href="#tick-icon"/></svg><span>Block Heat<br>&amp; Noise</span></li>
    <li><svg class="icon"><use href="#tick-icon"/></svg><span>Total<br>Light<br>Control</span></li>
  </ul>
  <div class="offer"><div class="tag">UP TO</div><div class="big">40</div><div class="pct">%</div><div class="off">OFF</div></div>
  <svg class="badge"><use href="#seal"/></svg>
  <div class="brand"><div class="brand-mark"></div><div class="brand-name">Portals Drapes<br>&amp; Louvres</div></div>
  <div class="cta"><div class="cta-line">Book a FREE quote TODAY!</div><div class="phone"><svg><use href="#phone-icon"/></svg>9471 2658</div><div class="address"><svg><use href="#pin-icon"/></svg>482 Upper Wattleby Road, Kestrel Heights</div></div>
</section>

<!-- Security Doors -->
<section class="ad c2 r2">
  <div class="sale-band">SALE NOW ON</div>
  <div class="title-band"><h2 class="product-name">Security Doors</h2><p class="site">www.portalsdrapesandlouvres.com.au</p></div>
  <div class="frame"></div><div class="frame-gap"></div>
  <div class="photo" role="img" aria-label="White security door with diamond mesh at a home entrance" style="background:linear-gradient(90deg,#e9ecef 0%,#5d6f86 20%,#f3f3f3 35%,#2c2c2c 50%,#f3f3f3 65%,#7b8c9a 85%,#5a3a2c 100%)"></div>
  <ul class="features">
    <li><svg class="icon"><use href="#tick-icon"/></svg><span>3 Point<br>Locking</span></li>
    <li><svg class="icon"><use href="#tick-icon"/></svg><span>Premium<br>Mesh</span></li>
    <li><svg class="icon"><use href="#tick-icon"/></svg><span>Custom<br>Made</span></li>
  </ul>
  <div class="offer"><div class="tag">FROM</div><div class="price solo">$750</div></div>
  <svg class="badge"><use href="#seal"/></svg>
  <div class="brand"><div class="brand-mark"></div><div class="brand-name">Portals Drapes<br>&amp; Louvres</div></div>
  <div class="cta"><div class="cta-line order">ORDER NOW</div><div class="phone"><svg><use href="#phone-icon"/></svg>9471 2658</div><div class="address"><svg><use href="#pin-icon"/></svg>482 Upper Wattleby Road, Kestrel Heights</div></div>
</section>

<!-- Blinds & Sheers -->
<section class="ad c3 r2">
  <div class="sale-band">SALE NOW ON</div>
  <div class="title-band"><h2 class="product-name">Blinds &amp; Sheers</h2><p class="site">www.portalsdrapesandlouvres.com.au</p></div>
  <div class="frame"></div><div class="frame-gap"></div>
  <div class="photo" role="img" aria-label="Covered timber-ceiling patio with sheer blinds and paved courtyard" style="background:linear-gradient(180deg,#b5865a 0%,#a77b52 25%,#4f5a4a 45%,#9a9a94 70%,#c9c6c0 100%)"></div>
  <ul class="features">
    <li><svg class="icon"><use href="#tick-icon"/></svg><span>Huge Range<br>of Fabrics</span></li>
    <li><svg class="icon"><use href="#tick-icon"/></svg><span>Modern<br>Soft Finish</span></li>
    <li><svg class="icon"><use href="#tick-icon"/></svg><span>Perfect for<br>Any Room</span></li>
  </ul>
  <div class="offer"><div class="tag">UP TO</div><div class="big">40</div><div class="pct">%</div><div class="off">OFF</div></div>
  <svg class="badge"><use href="#seal"/></svg>
  <div class="brand"><div class="brand-mark"></div><div class="brand-name">Portals Drapes<br>&amp; Louvres</div></div>
  <div class="cta"><div class="cta-line">Book a FREE quote TODAY!</div><div class="phone"><svg><use href="#phone-icon"/></svg>9471 2658</div><div class="address"><svg><use href="#pin-icon"/></svg>482 Upper Wattleby Road, Kestrel Heights</div></div>
</section>

</body>
</html>
```